Equipment Finance Specialist I work with companies who need the funds to buy their equipment

I would like a business card that stands out on the shelves. I want to be able to hand it to someone and say WOW. This card should have my logo.
You can put color into it I am very open on design and color

What my company does is we deal with dealerships that sell equipment such as Dump Trucks garbage trucks tractors trailers. Customers get referred to us and depending on their time in business we will ask for the following items

Companies that have been in business for more than two years we have a credit application program up to 250K . With this program we need the following items Credit application filled out(which is what I would like to be able for the customer to click on my website to get.) as well as three current month bank statements.

Deals over 250k we will need the following items

2 years business tax returns
2 years personal tax returns
Profit & Loss statement
Personal Financial Statement

what we do
100% FINANCING
SEASONAL PAYMENTS
LOAN BALLOON PAYMENTS
TRAC LEASING
LOW-INTEREST REFINANCING RATES
DEBT CONSOLIDATION

We specialize in creative financing solutions and offer a variety of reliable, flexible and expandable lending choices.

Target Market(s)

Trucking Companies

Industry/Entity Type

Trucking Company

Contact Information for Business Card

* $250,000 Application only Program
* Loans from $30,000 to 5,000,000
* Competitive Interest Rates

Font styles to use
Serif
Sans Serif

Colors

Designer to choose colors to be used in the design.

Requirements
Must have
• On the back of the card.
• * $250,000 Application only Program
• * Loans from $30,000 to 5,000,000
• My name, email, website. address
• * Competitive Interest Rates
• * 100% Financing
Nice to have
• I want my logo to pop on the card
• My logo is the great one I would like to use
Should not have
• I am up for your creativity as well

```html
<!DOCTYPE html>
<html lang="en">
<head>
<meta charset="utf-8">
<title>Summit Financing – Business Card</title>
<link rel="stylesheet" href="https://fonts.googleapis.com/css2?family=Montserrat:wght@700;800&family=Source+Sans+3:wght@400;600&display=swap">
<style>
  :root {
    --bg: #2a2a2b;
    --red: #bd0d2f;
    --navy: #0c2c6a;
    --white: #ffffff;
    --ink: #444444;
    --truck-light: #f3f1f2;
    --truck-tone: #d9c9cf;
  }
  * { margin: 0; padding: 0; box-sizing: border-box; }
  html, body { width: 1125px; height: 1200px; overflow: hidden; }
  body { background: var(--bg); position: relative; font-family: "Source Sans 3", sans-serif; }

  .card {
    position: absolute;
    left: 150px;
    width: 825px;
    height: 470px;
    border-radius: 24px;
    overflow: hidden;
  }
  .card--front { top: 98px; background: var(--red); }
  .card--back { top: 631px; background: var(--white); }

  .front-art { position: absolute; inset: 0; width: 100%; height: 100%; }

  .contact { position: absolute; left: 46px; top: 42px; color: var(--white); }
  .contact__name { font-family: "Montserrat", sans-serif; font-weight: 800; font-size: 29px; letter-spacing: 0.5px; line-height: 1.1; }
  .contact__title { font-family: "Montserrat", sans-serif; font-weight: 700; font-size: 21px; letter-spacing: 0.5px; margin-top: 2px; }
  .contact__address { font-size: 24px; line-height: 27px; margin-top: 22px; }
  .contact__list { list-style: none; margin-top: 13px; font-size: 23px; line-height: 27px; }
  .contact__list li { display: flex; align-items: center; gap: 14px; }
  .contact__list svg { width: 20px; height: 20px; flex: none; }

  .brand {
    position: absolute; left: 0; right: 0; top: 170px;
    display: flex; justify-content: center; align-items: center; gap: 18px;
  }
  .brand__dot { width: 64px; height: 64px; border-radius: 50%; background: var(--navy); }
  .brand__name {
    font-family: "Source Sans 3", sans-serif; font-weight: 600;
    font-size: 58px; color: var(--navy); letter-spacing: 1px;
  }

  .offers {
    position: absolute; left: 0; right: 0; top: 372px;
    text-align: center; color: var(--ink); font-size: 21px; line-height: 26px;
  }
  .offers__dot { display: inline-block; width: 9px; height: 9px; border-radius: 50%; background: var(--navy); margin: 0 4px 2px; }
</style>
</head>
<body>
  <section class="card card--front">
    <svg class="front-art" viewBox="0 0 825 470" aria-hidden="false">
      <path d="M530 0 H825 V470 H470 C640 430 760 330 780 200 C790 110 720 30 530 0 Z" fill="var(--navy)"/>
      <ellipse cx="580" cy="220" rx="215" ry="215" fill="var(--red)"/>
      <path d="M355 260 C350 360 420 440 480 470 H520 C430 430 370 360 355 260 Z" fill="var(--navy)"/>
      <rect role="img" aria-label="Illustration of a dump truck cab with stars on the hood" x="370" y="55" width="400" height="345" rx="40" fill="url(#truckTone)"/>
      <defs>
        <linearGradient id="truckTone" x1="0" y1="0" x2="1" y2="1">
          <stop offset="0" stop-color="var(--truck-light)"/>
          <stop offset="1" stop-color="var(--truck-tone)"/>
        </linearGradient>
      </defs>
    </svg>

    <div class="contact">
      <h1 class="contact__name">MARK HALDEN</h1>
      <p class="contact__title">PRESIDENT</p>
      <p class="contact__address">4127 Harbor View Road<br>Lake Crest, NY 11020</p>
      <ul class="contact__list">
        <li><svg viewBox="0 0 20 20"><path d="M3 7 C3 4 17 4 17 7 L15 9 L12 7 V6 H8 V7 L5 9 Z M5 10 H15 L17 16 H3 Z" fill="#fff"/><circle cx="10" cy="13" r="2" fill="var(--red)"/></svg>555 0142 7788</li>
        <li><svg viewBox="0 0 20 20"><rect x="2" y="5" width="16" height="11" rx="1" fill="#fff"/><path d="M2 6 L10 11 L18 6" stroke="var(--red)" stroke-width="1.5" fill="none"/></svg>mark@summitfinancing.com</li>
        <li><svg viewBox="0 0 20 20"><circle cx="10" cy="10" r="8" fill="#fff"/><path d="M6 6 C9 7 8 10 11 11 C12 13 10 15 9 17" stroke="var(--red)" stroke-width="1.6" fill="none"/></svg>www.summitfinancing.com</li>
      </ul>
    </div>
  </section>

  <section class="card card--back">
    <div class="brand">
      <span class="brand__dot"></span>
      <span class="brand__name">SUMMIT FINANCING</span>
    </div>
    <p class="offers">
      $250,000 Application only Program<span class="offers__dot"></span>Loans from $30,000 to 5,000,000<br>
      Competitive Interest Rates <span class="offers__dot"></span>100% Financing
    </p>
  </section>
</body>
</html>
```